BorrowNest Website design, we are a home loan / lending company

We are a finance broking company that can do mortgages / home loans, Car Loans, Commercial Loans, SMSF Loans, Business Loans, Personal Loans
We are looking for a simple website, not too busy, easy to navigate, something that prompts customers to action or call us.
I like the simplicity of the following websites:
https://www.velkarafinance.com.au/ - I like this website front page. I was thinking I have my logo, the one with the black background appear , then the toolbar at the top perhaps?
https://trevix.com.au/business-loans# - on this page there are images under finance that works for you that I like that concept.
https://dunmerel.com.au/contact/ - I like the Make an Appointment page
https://trevix.com.au/about-us - Simple but effective page design

Target Market(s)

Home Loan Customer

Industry/Entity Type

Finance / Home Loans

Coding

Coded - Design and coding required

Number of Pages Required

5+ page

Font styles to use
Serif

Colors
0094D4
00A9DD
6FCCEA
C7EBF8
E9F6FB

Requirements
Must have
• The following Heading s - Contact Us, About Us, Our People, Make an Appointment, Loan Options, Calculators, Reviews. I want to use the Logo colours I have in the zip files I uploaded.
Nice to have
• Simple clean design

```html
<!DOCTYPE html>
<html lang="en">
<head>
<meta charset="utf-8">
<title>BorrowNest — Home Loans &amp; Lending</title>
<link rel="stylesheet" href="https://fonts.googleapis.com/css2?family=Roboto:wght@400;500;700;900&display=swap">
<style>
:root{
  --blue:#1679c9;
  --blue-bright:#2196e0;
  --blue-deep:#0f66b3;
  --sky:#e3f3fb;
  --sky-line:#c7ebf8;
  --ink:#111418;
  --text:#444b52;
  --muted:#666d74;
  --white:#ffffff;
  --footer:#121314;
  --star:#1679c9;
}
*{box-sizing:border-box;margin:0;padding:0}
html,body{width:1200px;height:4566px;overflow:hidden}
body{font-family:"Roboto",Arial,sans-serif;color:var(--ink);background:var(--white);position:relative}
a{color:inherit;text-decoration:none}

/* top bar */
.topbar{position:absolute;left:0;top:0;width:1200px;height:48px;background:var(--white)}
.topbar-band{position:absolute;left:430px;top:0;width:658px;height:48px;background:var(--blue)}
.topbar-item{position:absolute;top:0;height:48px;display:flex;align-items:center;gap:8px;color:var(--white);font-size:16px;white-space:nowrap}
.topbar-sep{position:absolute;left:621px;top:12px;width:1px;height:24px;background:rgba(255,255,255,.6)}
.topbar-cta{position:absolute;left:849px;top:0;width:239px;height:48px;background:var(--blue-bright);color:var(--white);font-size:16px;font-weight:500;display:flex;align-items:center;justify-content:center;letter-spacing:.2px}

/* nav */
.nav{position:absolute;left:0;top:48px;width:1200px;height:72px;background:var(--white);border-bottom:1px solid #e8e8e8}
.brand{position:absolute;left:115px;top:12px;font-size:40px;font-weight:700;letter-spacing:-1px;color:var(--ink);line-height:48px}
.nav-links{position:absolute;top:0;height:72px;left:0;width:1200px}
.nav-links a{position:absolute;top:26px;font-size:16px;font-weight:500;color:var(--ink)}
.nav-links a.active{color:var(--blue)}
.nav-links a.active::after{content:"";position:absolute;left:0;right:0;top:32px;height:3px;background:var(--blue)}

/* hero */
.hero{position:absolute;left:0;top:120px;width:1200px;height:648px;background:linear-gradient(100deg,#3a2a22 0%,#6b4a32 35%,#9a7a52 60%,#c9a86a 80%,#e6c98c 100%)}
.hero-shade{position:absolute;inset:0;background:linear-gradient(90deg,rgba(0,0,0,.45) 0%,rgba(0,0,0,.15) 55%,rgba(0,0,0,0) 100%)}
.hero h1{position:absolute;left:112px;top:190px;font-size:78px;font-weight:700;color:var(--white);letter-spacing:-.5px;line-height:90px}
.hero p{position:absolute;left:117px;top:290px;width:480px;font-size:20px;line-height:36px;color:var(--white)}
.btn{display:flex;align-items:center;justify-content:center;background:var(--blue);color:var(--white);font-weight:700;letter-spacing:.3px;border-radius:2px}
.hero .btn{position:absolute;left:115px;top:392px;width:231px;height:50px;font-size:16px}
.hero-arrow{position:absolute;top:290px}
.hero-dots{position:absolute;top:598px;left:552px;display:flex;gap:16px}
.hero-dots span{width:12px;height:12px;border-radius:50%;background:rgba(255,255,255,.55)}
.hero-dots span.on{background:var(--white)}

.section-title{position:absolute;left:0;width:1200px;text-align:center;font-weight:500;color:var(--ink)}

/* finance */
.finance{position:absolute;left:0;top:768px;width:1200px;height:514px;background:var(--sky)}
.finance .section-title{top:66px;font-size:37px}
.finance .lead{position:absolute;left:0;width:1200px;top:122px;text-align:center;font-size:18px;color:var(--ink)}
.fcard{position:absolute;top:184px;width:233px;height:257px;background:var(--white);box-shadow:0 2px 8px rgba(0,0,0,.06);text-align:center}
.fcard .icon{position:absolute;left:70px;top:29px;width:94px;height:94px;border-radius:50%;background:var(--blue);display:flex;align-items:center;justify-content:center}
.fcard h3{position:absolute;left:0;right:0;top:140px;font-size:21px;font-weight:700}
.fcard p{position:absolute;left:16px;right:16px;top:180px;font-size:14px;line-height:23px;color:var(--muted)}

/* about */
.about{position:absolute;left:0;top:1282px;width:1200px;height:632px;background:var(--white)}
.about-tint{position:absolute;left:120px;top:68px;width:316px;height:470px;background:linear-gradient(180deg,#dff2f8,#eef8fb)}
.about-photo{position:absolute;left:165px;top:113px;width:429px;height:431px;background:linear-gradient(135deg,#5d6f86 0%,#8b9bb0 40%,#c7ced6 70%,#7d8794 100%)}
.about h2{position:absolute;left:656px;top:142px;font-size:38px;font-weight:500}
.about p{position:absolute;left:656px;width:432px;font-size:14.5px;line-height:27.5px;color:var(--text)}
.about .btn{position:absolute;left:656px;top:473px;width:169px;height:53px;font-size:16px}

/* offers */
.offers{position:absolute;left:0;top:1914px;width:1200px;height:1096px;background:var(--sky)}
.offers .section-title{top:86px;font-size:37px}
.ocard{position:absolute;width:311px;height:408px;background:var(--white);text-align:center;box-shadow:0 2px 8px rgba(0,0,0,.05)}
.ocard .photo{position:absolute;left:0;top:0;width:311px;height:213px}
.ocard h3{position:absolute;left:0;right:0;top:233px;font-size:27px;font-weight:500}
.ocard p{position:absolute;left:24px;right:24px;top:277px;font-size:14.5px;line-height:27px;color:var(--muted)}
.ocard .more{position:absolute;left:0;right:0;top:363px;font-size:16px;font-weight:500;color:var(--blue);text-decoration:underline}
.ocard.hover::after{content:"";position:absolute;left:0;right:0;bottom:0;height:5px;background:var(--blue)}

/* reviews */
.reviews{position:absolute;left:0;top:3010px;width:1200px;height:533px;background:linear-gradient(180deg,var(--blue) 0%,var(--blue-deep) 100%)}
.reviews .section-title{top:74px;font-size:42px;color:var(--white)}
.score{position:absolute;left:90px;top:230px;width:202px;text-align:center;color:var(--white)}
.score .num{font-size:66px;font-weight:700;line-height:70px}
.score .stars{font-size:18px;letter-spacing:3px;margin-top:2px}
.score .count{font-size:15px;line-height:23px;margin-top:6px}
.rev-arrow{position:absolute;top:320px}
.rcard{position:absolute;top:166px;width:320px;height:282px;background:var(--white);padding:26px 28px}
.rcard .stars{color:var(--star);font-size:17px;letter-spacing:2px}
.rcard h4{font-size:18px;font-weight:700;margin-top:12px}
.rcard p{font-size:14px;line-height:26px;color:var(--text);margin-top:12px}
.rcard .name{font-size:17px;font-weight:500;margin-top:12px}
.rcard .role{font-size:14.5px;color:var(--blue);margin-top:2px}

/* blog */
.blog{position:absolute;left:0;top:3543px;width:1200px;height:651px;background:var(--white)}
.blog .section-title{top:84px;font-size:37px}
.bcard{position:absolute;top:146px;width:314px;height:418px;background:var(--white);box-shadow:0 2px 10px rgba(0,0,0,.08)}
.bcard .photo{position:absolute;left:0;top:0;width:314px;height:222px}
.bcard h4{position:absolute;left:13px;right:13px;top:240px;font-size:16px;font-weight:500;line-height:25px;text-transform:uppercase}
.bcard p{position:absolute;left:13px;right:13px;top:297px;font-size:13.5px;line-height:25px;color:var(--muted)}
.bcard .more{position:absolute;left:13px;top:380px;font-size:13px;font-weight:700;color:var(--blue);text-decoration:underline}

/* footer */
.footer{position:absolute;left:0;top:4194px;width:1200px;height:372px;background:var(--footer);color:var(--white)}
.footer .brand{left:115px;top:64px;font-size:36px;color:var(--white)}
.socials{position:absolute;left:148px;top:135px;display:flex;gap:7px}
.socials span{width:30px;height:30px;border-radius:50%;background:var(--white)}
.fcol{position:absolute;top:76px}
.fcol h5{font-size:16px;font-weight:700;text-transform:uppercase;letter-spacing:.3px;margin-bottom:22px}
.fcol ul{list-style:none}
.fcol li{font-size:13.5px;line-height:28.5px}
.contact-row{display:flex;gap:10px;font-size:13.5px;line-height:22px;margin-bottom:18px;align-items:flex-start}
.contact-row .dot{flex:none;width:28px;height:28px;border-radius:50%;background:var(--blue);display:flex;align-items:center;justify-content:center}
.sub-text{font-size:13.5px;line-height:28px;width:230px}
.sub-form{display:flex;margin-top:16px}
.sub-form .field{width:214px;height:46px;background:var(--white);color:#8a8f94;font-size:14px;display:flex;align-items:center;gap:8px;padding-left:16px}
.sub-form .go{width:50px;height:46px;background:var(--blue);display:flex;align-items:center;justify-content:center}
.footer-rule{position:absolute;left:112px;top:302px;width:976px;height:1px;background:#3a3c3f}
.copyright{position:absolute;left:0;top:326px;width:1200px;text-align:center;font-size:13px}
</style>
</head>
<body>

<header class="topbar">
  <div class="topbar-band"></div>
  <div class="topbar-item" style="left:457px">
    <svg width="15" height="15" viewBox="0 0 24 24"><path fill="#fff" d="M6.6 10.8a15.1 15.1 0 0 0 6.6 6.6l2.2-2.2c.3-.3.7-.4 1-.2 1.1.4 2.3.6 3.6.6.6 0 1 .4 1 1V20c0 .6-.4 1-1 1A17 17 0 0 1 3 4c0-.6.4-1 1-1h3.5c.6 0 1 .4 1 1 0 1.3.2 2.5.6 3.6.1.3 0 .7-.2 1z"/></svg>
    +1 555-014-2290
  </div>
  <div class="topbar-sep"></div>
  <div class="topbar-item" style="left:642px">
    <svg width="15" height="15" viewBox="0 0 24 24"><path fill="#fff" d="M22 2 2 10.5l7 2.5 2.5 7L22 2zm-11 11.5-1-3 9-7-8 10z"/></svg>
    info@borrownest.com
  </div>
  <a class="topbar-cta" href="#">MAKE AN APPOINTMENT</a>
</header>

<nav class="nav">
  <div class="brand">BorrowNest</div>
  <div class="nav-links">
    <a class="active" href="#" style="left:425px">Home</a>
    <a href="#" style="left:497px">About Us</a>
    <a href="#" style="left:596px">Our People</a>
    <a href="#" style="left:705px">Loan Options</a>
    <a href="#" style="left:830px">Calculators</a>
    <a href="#" style="left:941px">Reviews</a>
    <a href="#" style="left:1030px">Contact</a>
  </div>
</nav>

<section class="hero" role="img" aria-label="Smiling family with a child on the father's shoulders outside a brick home at sunset">
  <div class="hero-shade"></div>
  <h1>BorrowNest</h1>
  <p>Lorem ipsulor sit amet, conetr adipiscing elit, sed do eiusmod tempor</p>
  <a class="btn" href="#">MAKE AN APPOINTMENT</a>
  <svg class="hero-arrow" style="left:70px" width="22" height="40" viewBox="0 0 22 40"><path d="M20 2 2 20l18 18" fill="none" stroke="#fff" stroke-width="2"/></svg>
  <svg class="hero-arrow" style="left:1108px" width="22" height="40" viewBox="0 0 22 40"><path d="m2 2 18 18L2 38" fill="none" stroke="#fff" stroke-width="2"/></svg>
  <div class="hero-dots"><span></span><span class="on"></span><span></span><span></span></div>
</section>

<section class="finance">
  <h2 class="section-title">Finance that works for you</h2>
  <p class="lead">Apply for a business loan in 7 minutes and get a decision within 24 hours.</p>

  <div class="fcard" style="left:115px">
    <div class="icon"><svg width="50" height="50" viewBox="0 0 50 50" fill="none" stroke="#fff" stroke-width="2"><circle cx="25" cy="25" r="11"/><path d="M25 18v14M28.5 20.5h-5a2.5 2.5 0 0 0 0 5h3a2.5 2.5 0 0 1 0 5h-5.5"/><path d="M6 16h8M4 22h6M6 34h8M36 16h8M40 28h6M36 34h8"/></svg></div>
    <h3>Help with cash flow</h3>
    <p>Access working capital to keep your business running smoothly.</p>
  </div>
  <div class="fcard" style="left:362px">
    <div class="icon"><svg width="50" height="50" viewBox="0 0 50 50" fill="none" stroke="#fff" stroke-width="2"><path d="M10 8h5l6 26h18"/><rect x="19" y="12" width="12" height="10"/><rect x="27" y="18" width="12" height="12"/><circle cx="22" cy="39" r="3"/><circle cx="36" cy="39" r="3"/></svg></div>
    <h3>Purchase inventory</h3>
    <p>Scale your business with new tools, inventory, or equipment.</p>
  </div>
  <div class="fcard" style="left:608px">
    <div class="icon"><svg width="50" height="50" viewBox="0 0 50 50" fill="none" stroke="#fff" stroke-width="2"><circle cx="27" cy="15" r="8"/><path d="M27 10v10M29.5 12h-3.5a1.8 1.8 0 0 0 0 3.6h2a1.8 1.8 0 0 1 0 3.6h-3.5"/><path d="M6 32h8l8 3h8a2 2 0 0 1 0 4h-8M14 42l10 2 18-8a2 2 0 0 0-2-4l-10 4"/></svg></div>
    <h3>Pay for overheads</h3>
    <p>Cover operating costs, including staff, utilities, and other bills.</p>
  </div>
  <div class="fcard" style="left:854px">
    <div class="icon"><svg width="50" height="50" viewBox="0 0 50 50" fill="none" stroke="#fff" stroke-width="2"><rect x="14" y="8" width="26" height="16" rx="2"/><path d="M14 14h26M20 20h8"/><circle cx="16" cy="34" r="5"/><circle cx="32" cy="34" r="5"/><path d="M20 31l8 0M18 28l6-4"/></svg></div>
    <h3>Repay debt</h3>
    <p>Refinance business debt into manageable repayments.</p>
  </div>
</section>

<section class="about">
  <div class="about-tint"></div>
  <div class="about-photo" role="img" aria-label="Broker meeting with clients across a desk, reviewing loan papers"></div>
  <h2>About Us</h2>
  <p style="top:212px">Lorem ipsum dolor sit amet, consectedipiscing elit, sed do eiusmod tempor incididunt ut labore magna aliqua. Quis ipsum suspendisse ultrices gravida. Risus commodo viverra maecenas accumsan lacus vel facilisis. Lorem ipsum dolor sit amet, consectedipiscing elit, sed do eiusmod tempor incididunt</p>
  <p style="top:366px">Lorem ipsum dolor sit amet, consectedipiscing elit, sed do eiusmod tempor incididunt ut labore magna aliqua. Quis ipsum suspendisse ultrices gravida. Risus commodo</p>
  <a class="btn" href="#">LEARN MORE</a>
</section>

<section class="offers">
  <h2 class="section-title">What We Offer</h2>

  <div class="ocard" style="left:115px;top:165px">
    <div class="photo" role="img" aria-label="Small house model and keys on a desk during a mortgage signing" style="background:linear-gradient(135deg,#5b4a3c,#a48466 55%,#d9c7b0)"></div>
    <h3>Mortgages</h3>
    <p>Lorem ipsum dolor sit amet, consectetur adipiscing elit, semod tempor incididunt ut labore et dolore magna aliqua.</p>
    <a class="more" href="#">LEARN MORE</a>
  </div>
  <div class="ocard hover" style="left:447px;top:165px">
    <div class="photo" role="img" aria-label="Hand gesturing okay above a toy red car on an envelope" style="background:linear-gradient(135deg,#4a3a30,#8c6a52 50%,#d2a070)"></div>
    <h3>Car Loans</h3>
    <p>Lorem ipsum dolor sit amet, consectetur adipiscing elit, semod tempor incididunt ut labore et dolore magna aliqua.</p>
    <a class="more" href="#">LEARN MORE</a>
  </div>
  <div class="ocard" style="left:776px;top:165px">
    <div class="photo" role="img" aria-label="Business team discussing documents at an office table" style="background:linear-gradient(135deg,#6a5a50,#a09484 50%,#d8d2c8)"></div>
    <h3>Commercial Loans</h3>
    <p>Lorem ipsum dolor sit amet, consectetur adipiscing elit, semod tempor incididunt ut labore et dolore magna aliqua.</p>
    <a class="more" href="#">LEARN MORE</a>
  </div>

  <div class="ocard" style="left:115px;top:591px">
    <div class="photo" role="img" aria-label="Model house beside stacks of coins" style="background:linear-gradient(135deg,#7a8a5a,#b8b6a0 55%,#e4e2da)"></div>
    <h3>SMSF Loans</h3>
    <p>Lorem ipsum dolor sit amet, consectetur adipiscing elit, semod tempor incididunt ut labore et dolore magna aliqua.</p>
    <a class="more" href="#">LEARN MORE</a>
  </div>
  <div class="ocard" style="left:447px;top:591px">
    <div class="photo" role="img" aria-label="Two colleagues working at laptops in a modern office" style="background:linear-gradient(135deg,#3a3d40,#7c8284 50%,#c9cfcc)"></div>
    <h3>Business Loans</h3>
    <p>Lorem ipsum dolor sit amet, consectetur adipiscing elit, semod tempor incididunt ut labore et dolore magna aliqua.</p>
    <a class="more" href="#">LEARN MORE</a>
  </div>
  <div class="ocard" style="left:776px;top:591px">
    <div class="photo" role="img" aria-label="Woman reviewing paperwork at a desk by a window" style="background:linear-gradient(135deg,#a8a294,#d6d0c2 50%,#f0ede6)"></div>
    <h3>Personal Loans</h3>
    <p>Lorem ipsum dolor sit amet, consectetur adipiscing elit, semod tempor incididunt ut labore et dolore magna aliqua.</p>
    <a class="more" href="#">LEARN MORE</a>
  </div>
</section>

<section class="reviews">
  <h2 class="section-title">What People Are Saying</h2>
  <div class="score">
    <div class="num">4.98</div>
    <div class="stars">★★★★★</div>
    <div class="count">422 verified<br>customer reviews</div>
  </div>
  <svg class="rev-arrow" style="left:324px" width="16" height="32" viewBox="0 0 16 32"><path d="M14 2 2 16l12 14" fill="none" stroke="#fff" stroke-width="2"/></svg>
  <div class="rcard" style="left:369px">
    <div class="stars">★★★★★</div>
    <h4>HIGHLY RECOMMEND</h4>
    <p>Lorem ipsum dolor sit aet, consectetur adipiscing elit, sed do eiusmod tempor inct ut labore et dolore magna aliqua. Quis ipsum suspendisse</p>
    <div class="name">John Deo</div>
    <div class="role">Finibus Bonorum</div>
  </div>
  <div class="rcard" style="left:710px">
    <div class="stars">★★★★★</div>
    <h4>HIGHLY RECOMMEND</h4>
    <p>Lorem ipsum dolor sit aet, consectetur adipiscing elit, sed do eiusmod tempor inct ut labore et dolore magna aliqua. Quis ipsum suspendisse</p>
    <div class="name">John Deo</div>
    <div class="role">Finibus Bonorum</div>
  </div>
  <svg class="rev-arrow" style="left:1056px" width="16" height="32" viewBox="0 0 16 32"><path d="m2 2 12 14L2 30" fill="none" stroke="#fff" stroke-width="2"/></svg>
</section>

<section class="blog">
  <h2 class="section-title">Latest Blog</h2>
  <article class="bcard" style="left:112px">
    <div class="photo" role="img" aria-label="Family sitting on the floor of a new home among moving boxes" style="background:linear-gradient(135deg,#cfc6bc,#a88a6c 55%,#6e5846)"></div>
    <h4>The standard Lorem Ipsum passage, used since</h4>
    <p>At vero eos et accusamusto odio dignissimos ducimus qui blnditiis praesentium voluptatum deleniti atque corrupti quos</p>
    <a class="more" href="#">READ MORE »</a>
  </article>
  <article class="bcard" style="left:443px">
    <div class="photo" role="img" aria-label="Hands exchanging a house model over a laptop and contract" style="background:linear-gradient(135deg,#7e7a74,#b4aea4 50%,#d66e3c)"></div>
    <h4>The standard Lorem Ipsum passage, used since</h4>
    <p>At vero eos et accusamusto odio dignissimos ducimus qui blnditiis praesentium voluptatum deleniti atque corrupti quos</p>
    <a class="more" href="#">READ MORE »</a>
  </article>
  <article class="bcard" style="left:775px">
    <div class="photo" role="img" aria-label="Laptop screen showing personal loan charts beside a coffee cup" style="background:linear-gradient(135deg,#d8dde2,#8a98a6 50%,#3a4048)"></div>
    <h4>The standard Lorem Ipsum passage, used since</h4>
    <p>At vero eos et accusamusto odio dignissimos ducimus qui blnditiis praesentium voluptatum deleniti atque corrupti quos</p>
    <a class="more" href="#">READ MORE »</a>
  </article>
</section>

<footer class="footer">
  <div class="brand">BorrowNest</div>
  <div class="socials" aria-label="Social links"><span></span><span></span><span></span><span></span></div>

  <div class="fcol" style="left:408px">
    <h5>Quick Links</h5>
    <ul><li>Home</li><li>About Us</li><li>Our People</li><li>Loan Options</li><li>Reviews</li><li>Contact</li></ul>
  </div>

  <div class="fcol" style="left:571px">
    <h5>Contact Us</h5>
    <div class="contact-row"><span class="dot"><svg width="12" height="14" viewBox="0 0 24 28"><path fill="#fff" d="M12 0a10 10 0 0 0-10 10c0 7.5 10 18 10 18s10-10.5 10-18A10 10 0 0 0 12 0zm0 14a4 4 0 1 1 0-8 4 4 0 0 1 0 8z"/></svg></span><span>62 Wattle Street, Carlow<br>Heights 2150, Australia</span></div>
    <div class="contact-row"><span class="dot"><svg width="12" height="12" viewBox="0 0 24 24"><path fill="#fff" d="M6.6 10.8a15.1 15.1 0 0 0 6.6 6.6l2.2-2.2c.3-.3.7-.4 1-.2 1.1.4 2.3.6 3.6.6.6 0 1 .4 1 1V20c0 .6-.4 1-1 1A17 17 0 0 1 3 4c0-.6.4-1 1-1h3.5c.6 0 1 .4 1 1 0 1.3.2 2.5.6 3.6.1.3 0 .7-.2 1z"/></svg></span><span style="line-height:28px">+1 555 014 2290</span></div>
    <div class="contact-row"><span class="dot"><svg width="13" height="10" viewBox="0 0 26 20"><rect x="1" y="1" width="24" height="18" rx="2" fill="none" stroke="#fff" stroke-width="2"/><path d="m1 2 12 9 12-9" fill="none" stroke="#fff" stroke-width="2"/></svg></span><span style="line-height:28px">info@borrownest.com</span></div>
  </div>

  <div class="fcol" style="left:824px">
    <h5>Subscribe to our blog</h5>
    <p class="sub-text">Sign up today to get resources on how to attract and retain more customers!</p>
    <div class="sub-form">
      <div class="field"><svg width="14" height="11" viewBox="0 0 26 20"><rect x="1" y="1" width="24" height="18" rx="2" fill="none" stroke="#8a8f94" stroke-width="2"/><path d="m1 2 12 9 12-9" fill="none" stroke="#8a8f94" stroke-width="2"/></svg>Email Address</div>
      <div class="go"><svg width="18" height="18" viewBox="0 0 24 24"><path fill="#fff" d="M22 2 2 10.5l7 2.5 2.5 7L22 2zm-11 11.5-1-3 9-7-8 10z"/></svg></div>
    </div>
  </div>

  <div class="footer-rule"></div>
  <div class="copyright">Copyright © 2022. BorrowNest All Rights Reserved &nbsp;|&nbsp; Privacy Policy &nbsp;|&nbsp; Legal Info</div>
</footer>

</body>
</html>
```